Etiketten für Bio Seifen
Zielgruppe
Wir stellen hochwertig 'handgemachte' Bio-Seifen her. Die Zielgruppe ist von 3-99 Jahren und zusätzlich haben wir auch noch Seife für Hunde.
Der Firmenname ist 'Verdolina'
Aufgabenstellung
Das Etikett soll Bezug auf Natur, Bio, Nachhaltigkeit nehmen. Wir stellen uns 'weiche' Aquarellfarben vor...Seife: Lavendel, Calendular, 7 Kräuter etc.
Das Etikett soll auf eine Beutelschachtel. Die Schachtel hat eine Anmaße: Breite 55mm; Höhe 120mm; Tiefe 30mm
Das Etikett soll im vorderen- und hinteren Bereich zusammenhängend geklebt werden.
Das Etikett soll eine Abmaße von: Breite 51mm; Höhe 114mm haben (Vorderseite) Rückseite gleich.
Wir möchten die Produkte auch gerne nummerieren, d.h. jede Seife hat eine Nummer die nicht zu groß dargestellt werden soll aber trotzdem gut leserlich.
Wir haben noch ein paar Bilder hochgeladen wie wir uns das ungefähr vorstellen.

```html
<!DOCTYPE html>
<html lang="de">
<head>
<meta charset="utf-8">
<title>Verdolina Bio Seife – Etikett Lavendel</title>
<link href="https://fonts.googleapis.com/css2?family=Josefin+Sans:wght@300;400&family=Raleway:wght@300;400&family=Allura&display=swap" rel="stylesheet">
<style>
  :root {
    --page: #ffffff;
    --lavender-deep: #4b2a86;
    --lavender-mid: #7b82c8;
    --lavender-soft: #8f86cc;
    --lavender-rose: #9a7cc4;
    --frame-fill: rgba(110, 80, 170, 0.35);
    --label-white: #f4f1fb;
    --pattern-tone: #eceaf1;
  }
  * { box-sizing: border-box; margin: 0; padding: 0; }
  html, body {
    width: 1200px;
    height: 849px;
    overflow: hidden;
    background: var(--page);
  }
  .sheet {
    position: relative;
    width: 1200px;
    height: 849px;
  }
  .label {
    position: absolute;
    left: 440px;
    top: 195px;
    width: 207px;
    height: 460px;
    overflow: hidden;
  }
  .label-artwork {
    position: absolute;
    inset: 0;
    background:
      radial-gradient(ellipse at 70% 35%, rgba(120,140,210,0.55), transparent 60%),
      radial-gradient(ellipse at 30% 90%, rgba(170,120,200,0.6), transparent 55%),
      linear-gradient(180deg, var(--lavender-soft) 0%, #7f7cc6 45%, var(--lavender-mid) 70%, var(--lavender-rose) 100%);
  }
  .label-frame {
    position: absolute;
    left: 10px;
    right: 8px;
    top: 149px;
    height: 131px;
    border: 1.2px solid var(--lavender-deep);
    background: var(--frame-fill);
    text-align: center;
    padding-top: 18px;
  }
  .brand-name {
    font-family: "Raleway", sans-serif;
    font-weight: 300;
    font-size: 19px;
    letter-spacing: 1.5px;
    color: var(--label-white);
    line-height: 1;
  }
  .product-type {
    font-family: "Raleway", sans-serif;
    font-weight: 400;
    font-size: 7.5px;
    letter-spacing: 0.8px;
    color: var(--lavender-deep);
    margin-top: 6px;
  }
  .handmade {
    font-family: "Allura", cursive;
    font-size: 11px;
    color: rgba(75, 42, 134, 0.7);
    margin-top: 1px;
    line-height: 1;
  }
  .scent {
    font-family: "Josefin Sans", sans-serif;
    font-weight: 400;
    font-size: 17px;
    letter-spacing: 0.5px;
    color: var(--lavender-deep);
    line-height: 1;
    margin-top: 2px;
  }
  .scent-initial { font-size: 23px; }
  .number {
    font-family: "Josefin Sans", sans-serif;
    font-weight: 400;
    font-size: 8.5px;
    letter-spacing: 0.5px;
    color: var(--label-white);
    margin-top: 4px;
  }
  .swatches {
    position: absolute;
    left: 723px;
    top: 308px;
    display: flex;
    flex-direction: column;
    gap: 13px;
  }
  .swatch {
    width: 70px;
    height: 70px;
    border-radius: 50%;
    border: 1.5px solid var(--lavender-deep);
  }
  .swatch-colour { background: var(--lavender-mid); }
  .swatch-pattern {
    background: radial-gradient(circle at 50% 45%, #ffffff 0%, var(--pattern-tone) 100%);
  }
</style>
</head>
<body>
  <main class="sheet">
    <section class="label">
      <div class="label-artwork" role="img" aria-label="Lavendelfarbener Aquarellgrund mit feinem hellem Blätterrankenmuster"></div>
      <div class="label-frame">
        <p class="brand-name">VERDOLINA</p>
        <p class="product-type">BIO SEIFE</p>
        <p class="handmade">Handgemachte</p>
        <p class="scent"><span class="scent-initial">L</span>AVENDE<span class="scent-initial">L</span></p>
        <p class="number">NR. 1</p>
      </div>
    </section>
    <aside class="swatches">
      <div class="swatch swatch-colour" role="img" aria-label="Farbmuster Lavendelblau"></div>
      <div class="swatch swatch-pattern" role="img" aria-label="Musterprobe helle Blätterranken auf Weiß"></div>
    </aside>
  </main>
</body>
</html>
```